"Outside the Box" Newsletter Design Project-Communications Company

I am looking for an Internal newsletter for a communications company that will be sent to our sales and leadership team.
This newsletter will deliver forecasting, sales results, stack rankings for the sales reps, total team results, corporate updates, success stories and updates from Training/Operations/Sales/Marketing (could be a box for each)I would also need a couple sections with a blank header and box to add info as needed, if something comes up that is not set in stone weekly.
I am looking for a template that looks sharp and professional that i can use every week by just dropping content in, (text and possibly an employee picture) I will need it in a format (possibly word) that the will keep the text in line when I drop it in each week. Once complete I can save to a pdf and would like to have the ability to drop it into the body of an email.

We have a racecar theme that we use when training our sales folks so we would like a little bit of that to the newsletter and also incorporate our color scheme from our company.

I would like four versions of the newsletter..all would match other than the title.
1. Week 1 title - Start your engines
2. Week 2 title - Looking for suggestions
3. Week 3 title - Looking for suggestions
4. Week 4 title - Approaching the finish line, this version would also include an employee spotlight, one seperate section.

If we could include a few pics around racing that would be good, not over the top, just a few to give it a little of that feel. Maybe a checkered flag with the QV logo on it, a racecar..anything else that may make sense.

I will attach our logo and our organization is called SMB (small/medium business) so that should also be placed on there somewhere. Final design would need to be two pages, sharp professional feel, my Vice President likes a very clean look, not too busy. I have also attached a sample newsletter from another group in our company, ours will not have as much content, we are much smaller but this is a sample (on a smaller scale)of what we are looking for. The company look and feel is what we want to follow. Thank you

Target Market(s)

Our Internal sales team.

Industry/Entity Type

Communications

Requirements
Must have
• Ability to update with my content without having things shift and fall out of line..format that will make that easy and then able to save to PDF..2 pages long.
Nice to have
• HTML template to match.

```html
<!DOCTYPE html>
<html lang="en">
<head>
<meta charset="UTF-8">
<title>Sales Rankings – Stack Report</title>
<link rel="stylesheet" href="https://fonts.googleapis.com/css2?family=Open+Sans:wght@400;700&display=swap">
<style>
  :root {
    --page-bg: #efefef;
    --brand-purple: #853b97;
    --header-text: #ffffff;
    --row-white: #ffffff;
    --row-stripe: #f4f4f4;
    --cell-rule: #e2e2e2;
    --body-text: #333333;
  }
  * { box-sizing: border-box; margin: 0; padding: 0; }
  html, body {
    width: 940px;
    height: 1200px;
    overflow: hidden;
    background: var(--page-bg);
    font-family: "Open Sans", Verdana, sans-serif;
    color: var(--body-text);
  }
  .report-table {
    position: absolute;
    border-collapse: collapse;
    table-layout: fixed;
    background: var(--row-white);
    box-shadow: 0 1px 3px rgba(0, 0, 0, 0.12);
  }
  .rep-ranking { top: 15px; left: 31px; width: 880px; }
  .team-results { top: 829px; left: 32px; width: 879px; }

  .report-table th {
    background: var(--brand-purple);
    color: var(--header-text);
    font-size: 14px;
    font-weight: 700;
    line-height: 29px;
    height: 80px;
    text-align: left;
    vertical-align: middle;
    border-left: 1px solid rgba(255, 255, 255, 0.18);
  }
  .report-table th:first-child { border-left: none; }
  .report-table td {
    height: 44px;
    font-size: 13px;
    vertical-align: middle;
    border-left: 1px solid var(--cell-rule);
    white-space: nowrap;
  }
  .report-table td:first-child { border-left: none; }
  .report-table tbody tr:nth-child(even) td { background: var(--row-stripe); }

  /* rep ranking columns */
  .col-rank { width: 72px; }
  .col-rep { width: 278px; }
  .col-market { width: 268px; }
  .col-mtd { width: 146px; }
  .col-ptc { width: 116px; }
  .rep-ranking th.col-rank { padding-left: 13px; }
  .rep-ranking td.col-rank { padding-left: 24px; }
  .rep-ranking .col-rep { padding-left: 25px; }
  .rep-ranking .col-market { padding-left: 24px; }
  .rep-ranking .col-mtd { padding-left: 29px; }
  .rep-ranking .col-ptc { padding-left: 32px; }

  /* team results columns */
  .col-team { width: 326px; padding-left: 26px; }
  .col-sales { width: 117px; padding-left: 25px; }
  .col-rate { width: 104px; padding-left: 30px; }
  .col-july { width: 111px; }
  .col-june { width: 110px; }
  .col-total { width: 111px; }
  .team-results th.col-july,
  .team-results th.col-june,
  .team-results th.col-total { text-align: center; }
  .team-results td.col-july { padding-left: 40px; }
  .team-results td.col-june { padding-left: 41px; }
  .team-results td.col-total { padding-left: 38px; }
</style>
</head>
<body>

<table class="report-table rep-ranking">
  <thead>
    <tr>
      <th class="col-rank">Rank</th>
      <th class="col-rep">Sales Rep Name</th>
      <th class="col-market">Market</th>
      <th class="col-mtd">Total<br>MTD</th>
      <th class="col-ptc">Total<br>Ptc</th>
    </tr>
  </thead>
  <tbody>
    <tr><td class="col-rank">1</td><td class="col-rep">Hallorin, Mark D</td><td class="col-market">Dallas</td><td class="col-mtd">$20.000</td><td class="col-ptc">90%</td></tr>
    <tr><td class="col-rank">2</td><td class="col-rep">Hallorin, Mark D</td><td class="col-market">Denver</td><td class="col-mtd">$20.000</td><td class="col-ptc">90%</td></tr>
    <tr><td class="col-rank">3</td><td class="col-rep">Vellacott, Andrew P</td><td class="col-market">Chicago</td><td class="col-mtd">$20.000</td><td class="col-ptc">90%</td></tr>
    <tr><td class="col-rank">4</td><td class="col-rep">Vellacott, Andrew P</td><td class="col-market">Vellacott, Andrew P</td><td class="col-mtd">$20.000</td><td class="col-ptc">90%</td></tr>
    <tr><td class="col-rank">5</td><td class="col-rep">Vellacott, Andrew P</td><td class="col-market">Vellacott, Andrew P</td><td class="col-mtd">$20.000</td><td class="col-ptc">90%</td></tr>
    <tr><td class="col-rank">6</td><td class="col-rep">Vellacott, Andrew P</td><td class="col-market">Vellacott, Andrew P</td><td class="col-mtd">$20.000</td><td class="col-ptc">90%</td></tr>
    <tr><td class="col-rank">7</td><td class="col-rep">Hallorin, Mark D</td><td class="col-market">Dallas</td><td class="col-mtd">$20.000</td><td class="col-ptc">90%</td></tr>
    <tr><td class="col-rank">8</td><td class="col-rep">Hallorin, Mark D</td><td class="col-market">Denver</td><td class="col-mtd">$20.000</td><td class="col-ptc">90%</td></tr>
    <tr><td class="col-rank">9</td><td class="col-rep">Vellacott, Andrew P</td><td class="col-market">Chicago</td><td class="col-mtd">$20.000</td><td class="col-ptc">90%</td></tr>
    <tr><td class="col-rank">10</td><td class="col-rep">Vellacott, Andrew P</td><td class="col-market">Vellacott, Andrew P</td><td class="col-mtd">$20.000</td><td class="col-ptc">90%</td></tr>
    <tr><td class="col-rank">11</td><td class="col-rep">Vellacott, Andrew P</td><td class="col-market">Vellacott, Andrew P</td><td class="col-mtd">$20.000</td><td class="col-ptc">90%</td></tr>
    <tr><td class="col-rank">12</td><td class="col-rep">Vellacott, Andrew P</td><td class="col-market">Vellacott, Andrew P</td><td class="col-mtd">$20.000</td><td class="col-ptc">90%</td></tr>
    <tr><td class="col-rank">13</td><td class="col-rep">Hallorin, Mark D</td><td class="col-market">Dallas</td><td class="col-mtd">$20.000</td><td class="col-ptc">90%</td></tr>
    <tr><td class="col-rank">14</td><td class="col-rep">Hallorin, Mark D</td><td class="col-market">Denver</td><td class="col-mtd">$20.000</td><td class="col-ptc">90%</td></tr>
    <tr><td class="col-rank">15</td><td class="col-rep">Vellacott, Andrew P</td><td class="col-market">Chicago</td><td class="col-mtd">$20.000</td><td class="col-ptc">90%</td></tr>
    <tr><td class="col-rank">16</td><td class="col-rep">Vellacott, Andrew P</td><td class="col-market">Vellacott, Andrew P</td><td class="col-mtd">$20.000</td><td class="col-ptc">90%</td></tr>
  </tbody>
</table>

<table class="report-table team-results">
  <thead>
    <tr>
      <th class="col-team">Team Name<br>and Market Location</th>
      <th class="col-sales">MTD<br>Sales</th>
      <th class="col-rate">Mtd<br>Ptc</th>
      <th class="col-july">July<br>Points</th>
      <th class="col-june">June<br>Points</th>
      <th class="col-total">Total<br>Points</th>
    </tr>
  </thead>
  <tbody>
    <tr><td class="col-team">Team Marlow - Denver</td><td class="col-sales">$20.000</td><td class="col-rate">90%</td><td class="col-july">1</td><td class="col-june">2</td><td class="col-total">3</td></tr>
    <tr><td class="col-team">Team Marlow - Denver</td><td class="col-sales">$20.000</td><td class="col-rate">90%</td><td class="col-july">1</td><td class="col-june">2</td><td class="col-total">3</td></tr>
    <tr><td class="col-team">Team Marlow - Denver</td><td class="col-sales">$20.000</td><td class="col-rate">90%</td><td class="col-july">1</td><td class="col-june">2</td><td class="col-total">3</td></tr>
    <tr><td class="col-team">Team Marlow - Denver</td><td class="col-sales">$20.000</td><td class="col-rate">90%</td><td class="col-july">1</td><td class="col-june">2</td><td class="col-total">3</td></tr>
  </tbody>
</table>

</body>
</html>
```